Redesign existing website

We would like a redesign of the website http://www.vantelquery.com that creates a more modern, up to date look.

Vantel Query creates software for social science research and is focused on making the software user friendly and easy to use. We would like to convey seriousness, but also
a very up to date, just released look.

Feel free to modify the logo if you wish.

Target Market(s)

Academics, researchers

Industry/Entity Type

Software

Requirements
Must have
• The design should incorporate the same information as the current website.

```html
<!DOCTYPE html>
<html lang="en">
<head>
<meta charset="utf-8">
<title>Vantel Query</title>
<link rel="stylesheet" href="https://fonts.googleapis.com/css2?family=Open+Sans:wght@400;600&family=Questrial&display=swap">
<style>
:root{
  --nav-bg:#2b2b2b;
  --nav-active:#2552b5;
  --page-bg:#ececec;
  --brand-blue:#1f3a8f;
  --accent-blue:#2a4aa8;
  --sky:#5cc0e6;
  --text:#2a2a2a;
  --muted:#6b6b6b;
  --footer-bg:#15213f;
  --footer-text:#b9c0d1;
  --link-red:#c0121a;
  --white:#ffffff;
}
*{box-sizing:border-box;margin:0;padding:0}
html,body{width:1104px;height:1200px;overflow:hidden}
body{position:relative;background:linear-gradient(#f7f7f7,#e9e9e9 440px,#efefef);font-family:"Open Sans",sans-serif;color:var(--text)}
.abs{position:absolute}
.topnav{left:0;top:0;width:1104px;height:62px;background:var(--nav-bg);border-top:4px solid #3a3a3a;border-bottom:2px solid #4a4a4a}
.topnav ul{list-style:none;display:flex;position:absolute;left:99px;top:4px}
.topnav li{height:52px;line-height:50px;color:#eee;font-size:16px;padding:0 30px 0 0;margin-right:34px}
.topnav li.active{background:var(--nav-active);padding:0 24px;margin-right:36px}
.logo{left:86px;top:82px;display:flex;align-items:center;gap:10px}
.logo-dot{width:34px;height:34px;border-radius:50%;background:var(--brand-blue)}
.logo-name{font-family:"Questrial",sans-serif;font-size:24px;color:var(--brand-blue)}
.search{left:803px;top:130px;width:232px;height:27px;border:1px solid #ccc;border-radius:14px 0 0 14px;background:#fff;font-size:12px;color:#777;padding:5px 26px}
.search-btn{left:1005px;top:130px;width:30px;height:27px;background:#4fb8e6;border-radius:0 4px 4px 0}
.hero{left:74px;top:198px;width:962px;height:351px;border-radius:10px;overflow:hidden}
.hero-side{left:0;top:0;width:315px;height:351px;background:linear-gradient(180deg,#a2def3,#4cb4e0)}
.cta{left:23px;width:272px;height:101px;border:3px solid #fff;border-radius:14px;background:linear-gradient(#4f76d8,#2447b1);color:#fff;text-align:center;box-shadow:0 2px 4px rgba(0,0,0,.3)}
.cta b{display:block;font-weight:400;font-size:26px;margin-top:16px}
.cta span{font-size:16px}
.hero-photo{left:315px;top:0;width:647px;height:351px;background:linear-gradient(90deg,#4d5a3a,#c9d2c8 55%,#55613f)}
.caption{left:315px;top:282px;width:647px;height:69px;background:rgba(200,200,200,.75);font-size:25px;line-height:30px;color:#333;padding:4px 20px}
.dots{left:861px;top:313px;display:flex;gap:2px}
.dots i{width:20px;height:20px;border-radius:50%;background:#7fd0f0}
.dots i:first-child{background:#1f3a8f}
.panel{background:#fff;border-radius:12px}
.welcome{left:74px;top:569px;width:962px;height:250px;background:linear-gradient(#fff,#f3f3f3)}
.shot{left:58px;top:25px;width:290px;height:210px;background:linear-gradient(#c8dcf4,#eef3fa);transform:skewY(-2deg)}
.welcome h1{left:396px;top:34px;font-weight:400;font-size:26px;color:#222}
.welcome h1 .b{color:var(--brand-blue)}.welcome h1 .g{color:#777}
.welcome p{left:397px;width:545px;font-size:12.5px;line-height:21px}
.lower{left:74px;top:850px;width:962px;height:252px}
.col-head{width:247px;height:38px;background:linear-gradient(#fff,#dcdcdc);font-family:"Questrial",sans-serif;font-size:20px;color:var(--brand-blue);padding:3px 30px}
.label{font-size:12.5px}
.field{width:135px;height:27px;background:#dcdcdc}
.login-btn{left:141px;top:181px;width:87px;height:24px;border-radius:12px;background:linear-gradient(#6bc7f4,#1f6fc9);border:2px solid #164a9a;color:#fff;font-size:13px;text-align:center;line-height:19px}
.cal{width:32px;height:44px;border:2px solid #888;border-radius:4px;background:#fff;border-top:10px solid #c62828;font-size:15px;font-weight:600;text-align:center;line-height:26px}
.news{font-size:12.5px;line-height:21px;width:190px}
.portrait{left:690px;top:88px;width:85px;height:106px;background:linear-gradient(#9c8f86,#7a4a5e)}
.bio-name{left:784px;top:88px;width:160px;font-size:12.5px;line-height:21px;color:var(--brand-blue)}
.bio{left:783px;top:140px;width:190px;font-size:11px;line-height:18px}
.more{left:788px;top:202px;font-size:11px;color:var(--link-red)}
.footer{left:0;top:1126px;width:1104px;height:74px;background:var(--footer-bg);border-bottom:5px solid #2c3c66}
.social{left:113px;top:18px;display:flex;gap:14px}
.social i{width:27px;height:27px;border-radius:5px;background:#3a5fb0}
.social i:nth-child(2){background:#4cb9e8}.social i:nth-child(3){background:#e8732a}
.flinks{left:410px;top:10px;font-size:12px;color:var(--footer-text);word-spacing:2px}
.copy{left:430px;top:39px;font-size:12px;color:var(--footer-text)}
</style>
</head>
<body>
<nav class="abs topnav"><ul><li class="active">Home</li><li>Products</li><li>News</li><li>About us</li><li>Contact us</li></ul></nav>

<div class="abs logo"><span class="logo-dot"></span><span class="logo-name">Vantel Query</span></div>
<div class="abs search">Search</div>
<div class="abs search-btn"><svg width="30" height="27"><circle cx="14" cy="12" r="5" fill="none" stroke="#fff" stroke-width="2"/><line x1="18" y1="16" x2="22" y2="20" stroke="#fff" stroke-width="2.5"/></svg></div>

<section class="abs hero">
  <div class="abs hero-side">
    <div class="abs cta" style="top:45px"><b>Vantel Data Manager</b><span>Preview Release Available!</span></div>
    <div class="abs cta" style="top:185px"><b>Vantel Data Manager</b><span>Download Preview Release</span></div>
  </div>
  <div class="abs hero-photo" role="img" aria-label="Photo of a gravel road through a deep green rock cutting"></div>
  <div class="abs caption">Increasing the power and efficiency of<br>empirical social science research</div>
  <div class="abs dots"><i></i><i></i><i></i><i></i></div>
</section>

<section class="abs panel welcome">
  <div class="abs shot" role="img" aria-label="Screenshot of the data manager application window"></div>
  <h1 class="abs">Welcome to <span class="b">VANTEL</span> <span class="g">QUERY</span></h1>
  <p class="abs" style="top:90px">The mission of Vantel Query, Inc. is to produce software products that multiply the power and efficiency of empirical scientific research in the social sciences.</p>
  <p class="abs" style="top:153px">A central goal is to expand access to complex data sources and to the advanced methods of scientific investigation needed to analyze them.</p>
</section>

<section class="abs panel lower">
  <h2 class="abs col-head" style="left:25px;top:33px;font-weight:400;padding-left:71px">Login</h2>
  <span class="abs label" style="left:36px;top:96px">User Name &nbsp;&nbsp;:</span>
  <span class="abs field" style="left:132px;top:88px"></span>
  <span class="abs label" style="left:36px;top:137px">Password &nbsp;&nbsp;&nbsp;:</span>
  <span class="abs field" style="left:132px;top:129px"></span>
  <div class="abs login-btn">Login</div>

  <h2 class="abs col-head" style="left:366px;top:33px;font-weight:400">Latest News</h2>
  <div class="abs cal" style="left:381px;top:90px">15</div>
  <p class="abs news" style="left:430px;top:88px">An early access preview of the Vantel Data Manager is available.</p>
  <div class="abs cal" style="left:381px;top:160px">15</div>
  <p class="abs news" style="left:430px;top:154px">Plenary Session by Helen Hallworth - New approaches to complex data management</p>

  <h2 class="abs col-head" style="left:687px;top:33px;font-weight:400;padding-left:21px">About Us</h2>
  <div class="abs portrait" role="img" aria-label="Portrait photo of the company president"></div>
  <p class="abs bio-name">Martin Hallworth, President and CEO</p>
  <p class="abs bio">Martin Hallworth has compiled an impressive record of in the realm of empirical social science research.</p>
  <span class="abs more">View More &nbsp;&gt;&gt;</span>
</section>

<footer class="abs footer">
  <div class="abs social"><i></i><i></i><i></i></div>
  <div class="abs flinks">Privacy Policy &nbsp;&nbsp;&nbsp;| &nbsp;&nbsp;&nbsp;Terms &amp; Conditions &nbsp;&nbsp;&nbsp;| &nbsp;&nbsp;&nbsp;Contact Us</div>
  <div class="abs copy">Copyright © VantelQuery, All Rights Reserved</div>
</footer>
</body>
</html>
```